New Business Card Design Project LORVANTI-Italy

we are LORVANTI-Italy
our company in the market for 3 years we are luxury cosmetic company and its about time for a facelift :)
i will like to have elegant luxurious and unique business card
that will give the person that get it a unique, luxurious and elegant impression
I'm VERY OPEN FOR NEW IDEAS , even duo i add a few files of things that i see on line and i like them

i add my logo as well
my website is LORVANTI.COM
(if you would like to see the main style that we have)

Target Market(s)

adult that have money :)

Industry/Entity Type

Business

Contact Information for Business Card

Name - Dario Lorvanti
Position - CEO and CO Founder
address - 4817 E Halvern
telephone - 555-384-1926
email - dario@lorvanti.com
fax - 555-384-1926
website - LORVANTI.COM

Colors
000000
959595
fbee3e
ffffff

Requirements
Must have
• big logo in GOLD color
• elegant look
• impressive
Nice to have
• not must but maybe classy pattern background
• not must but maybe emblem
• maybe clear plastic business card
Should not have
• colors
• images

```html
<!DOCTYPE html>
<html lang="en">
<head>
<meta charset="utf-8">
<title>LORVANTI Italy – Business Card</title>
<link rel="stylesheet" href="https://fonts.googleapis.com/css2?family=Tinos:wght@400;700&family=Open+Sans:wght@400&display=swap">
<style>
  :root {
    --backdrop: #676767;
    --card-front: #1e1e1f;
    --card-back: #151515;
    --card-back-light: #2a2a2a;
    --gold: #d9b23c;
    --text-light: #e6e6e6;
    --text-muted: #cfcfcf;
  }
  html, body {
    margin: 0;
    padding: 0;
    width: 1200px;
    height: 900px;
    overflow: hidden;
    background: var(--backdrop);
  }
  .stage {
    position: relative;
    width: 1200px;
    height: 900px;
    background: var(--backdrop);
  }
  .card {
    position: absolute;
    top: 306px;
    width: 439px;
    height: 271px;
    border-radius: 10px;
    overflow: hidden;
  }
  .card--front { left: 149px; background: var(--card-front); }
  .card--back  { left: 608px; background: var(--card-back); }

  .holder-name {
    position: absolute;
    left: 25px;
    top: 35px;
    margin: 0;
    font: 700 17px/1 "Tinos", serif;
    color: var(--gold);
    letter-spacing: 0.3px;
  }
  .holder-role {
    position: absolute;
    left: 25px;
    top: 58px;
    margin: 0;
    font: 400 12px/1 "Open Sans", sans-serif;
    color: var(--text-light);
  }
  .contact-list {
    position: absolute;
    left: 25px;
    top: 150px;
    margin: 0;
    padding: 0;
    list-style: none;
  }
  .contact-list li {
    display: flex;
    align-items: center;
    height: 16px;
    font: 400 12px/1 "Open Sans", sans-serif;
    color: var(--text-light);
  }
  .contact-icon {
    width: 10px;
    height: 10px;
    margin-right: 6px;
    fill: var(--gold);
  }
  .contact-address {
    position: absolute;
    left: 24px;
    top: 230px;
    margin: 0;
    font: 400 12px/1 "Open Sans", sans-serif;
    color: var(--text-light);
  }

  .brand {
    position: absolute;
    text-align: center;
    color: var(--gold);
    font-family: "Tinos", serif;
    font-weight: 400;
  }
  .brand-name, .brand-origin { margin: 0; display: block; }
  .card--front .brand { left: 205px; top: 172px; width: 220px; }
  .card--front .brand-name { font-size: 40px; line-height: 1; letter-spacing: 1px; }
  .card--front .brand-origin { font-size: 16px; margin-top: 16px; letter-spacing: 1px; }

  .back-texture {
    position: absolute;
    inset: 0;
    background: radial-gradient(ellipse at 40% 30%, var(--card-back-light), var(--card-back) 75%);
  }
  .brand-seal {
    position: absolute;
    left: 170px;
    top: 36px;
    width: 96px;
    height: 96px;
    border: 3px solid var(--gold);
    border-radius: 50%;
    box-sizing: border-box;
  }
  .card--back .brand { left: 90px; top: 158px; width: 260px; }
  .card--back .brand-name { font-size: 45px; line-height: 1; letter-spacing: 1px; }
  .card--back .brand-origin { font-size: 17px; margin-top: 17px; letter-spacing: 1px; }
</style>
</head>
<body>
<main class="stage">

  <section class="card card--front" aria-label="Business card front">
    <h1 class="holder-name">DARIO LORVANTI</h1>
    <p class="holder-role">CEO and CO Founder</p>

    <ul class="contact-list">
      <li>
        <svg class="contact-icon" viewBox="0 0 10 10" aria-hidden="true"><path d="M2 0.5 L3.6 2.6 L2.7 3.6 Q3.8 5.9 6.4 7.3 L7.4 6.4 L9.5 8 L8.3 9.5 Q3.8 9 0.5 1.7 Z"/></svg>
        555-384-1926
      </li>
      <li>
        <svg class="contact-icon" viewBox="0 0 10 10" aria-hidden="true"><path d="M3 1 H7 V3 H9.5 V9.5 H0.5 V3 H3 Z M4 2 V3 H6 V2 Z"/></svg>
        555-384-1926
      </li>
      <li>
        <svg class="contact-icon" viewBox="0 0 10 10" aria-hidden="true"><path d="M0.5 2 H9.5 V8.5 H0.5 Z" /><path d="M0.5 2 L5 5.6 L9.5 2" fill="none" stroke="#1e1e1f" stroke-width="0.9"/></svg>
        dario@lorvanti.com
      </li>
      <li>
        <svg class="contact-icon" viewBox="0 0 10 10" aria-hidden="true"><circle cx="5" cy="5" r="4.5"/><path d="M0.5 5 H9.5 M5 0.5 Q2.5 5 5 9.5 M5 0.5 Q7.5 5 5 9.5" fill="none" stroke="#1e1e1f" stroke-width="0.7"/></svg>
        www.lorvanti.com
      </li>
    </ul>

    <p class="contact-address">4817 E Halvern</p>

    <div class="brand">
      <span class="brand-name">LORVANTI</span>
      <span class="brand-origin">ITALY</span>
    </div>
  </section>

  <section class="card card--back" aria-label="Business card back">
    <div class="back-texture" role="img" aria-label="Subtle dark tone-on-tone pattern background"></div>
    <div class="brand-seal" aria-hidden="true"></div>
    <div class="brand">
      <span class="brand-name">LORVANTI</span>
      <span class="brand-origin">ITALY</span>
    </div>
  </section>

</main>
</body>
</html>
```